Local Flower Farm Needs Business Card Design

I need business cards designed for a flower farm based in Eudora, Kansas.
Business Info:
We are a local cut flower farm located in Eudora, Kansas, founded by Corinne Haldwick. What started as a passion for agriculture and search for more joy in daily life has blossomed into a small business dedicated to providing the community with beautiful, fresh, and sustainable flowers. We specialize in local, seasonal blooms, ensuring that every petal reflects the care and dedication we pour into our craft. Our mission is to deliver the highest quality flowers directly to our customers through local farmers markets and to florists who share our commitment to sustainability. Join us in celebrating the beauty of nature, one bloom at a time!
Contact Details:
Corinne Haldwick
Owner
Phone 913-555-0147
Facebook: Rosalind Thorpe Gardens
Instagram: @RosalindThorpeGardens
Website: RosalindThorpeGardens.example
Target Market(s)
Wholesale to Florists and Direct to Consumer via Farmers Market
Industry/Entity Type
Florist, Farm
Contact Information for Business Card
Name, Contact Info, Logo
Look and feel
Each slider illustrates characteristics of the customer's brand and the style your logo design should communicate.

```html
<!DOCTYPE html>
<html lang="en">
<head>
<meta charset="utf-8">
<title>Rosalind Thorpe Gardens — Business Card</title>
<link rel="stylesheet" href="https://fonts.googleapis.com/css2?family=Cormorant+Garamond:wght@600&family=Gloock&family=Poppins:wght@400;500;700&display=swap">
<style>
  :root {
    --backdrop: #8f8f8f;
    --night: #0a2127;
    --paper: #ececec;
    --teal: #134d55;
    --ink: #10343a;
    --slate: #5d6466;
    --mist: #c4f1f6;
    --blush: #f6e6e1;
    --rule: #9aa5a6;
    --white: #ffffff;
  }
  * { box-sizing: border-box; margin: 0; padding: 0; }
  html, body { width: 964px; height: 1200px; overflow: hidden; }
  body { background: var(--backdrop); position: relative; font-family: "Poppins", sans-serif; }

  .card { position: absolute; left: 93px; width: 779px; height: 445px; overflow: hidden; }
  .card--front { top: 125px; background: var(--night); }
  .card--back { top: 630px; background: var(--paper); }

  .floral { position: absolute; }

  .brand-seal {
    position: absolute; border-radius: 50%;
    display: flex; align-items: center; justify-content: center; text-align: center;
    font-family: "Cormorant Garamond", serif; font-weight: 600;
    letter-spacing: 0.12em; line-height: 1.15; text-transform: uppercase;
  }
  .card--front .brand-seal {
    left: 258px; top: 74px; width: 264px; height: 264px;
    border: 1.5px solid rgba(255,255,255,0.75); color: var(--white); font-size: 30px;
  }
  .card--back .brand-seal {
    left: 65px; top: 96px; width: 218px; height: 218px;
    border: 1.5px solid var(--rule); color: var(--ink); font-size: 25px;
  }

  .web-address {
    position: absolute; left: 0; right: 0; top: 384px; text-align: center;
    color: var(--white); font-size: 17px; letter-spacing: 0.12em; font-weight: 400;
  }
  .web-address strong { font-weight: 700; }

  .person { position: absolute; left: 346px; top: 84px; font-family: "Gloock", serif; font-weight: 400; line-height: 1; }
  .person__first { display: block; font-size: 44px; color: var(--slate); }
  .person__last { display: block; font-size: 44px; color: var(--ink); margin-top: 1px; }
  .person__role {
    position: absolute; left: 346px; top: 180px;
    font-size: 16px; letter-spacing: 0.45em; color: var(--slate);
  }

  .divider { position: absolute; left: 346px; width: 345px; height: 1px; background: var(--rule); }
  .divider--top { top: 213px; }
  .divider--bottom { top: 300px; }

  .contact-pill {
    position: absolute; left: 346px; top: 227px; width: 30px; height: 61px;
    border-radius: 15px; background: var(--teal); overflow: hidden;
  }
  .contact-pill::after {
    content: ""; position: absolute; left: 0; right: 0; top: 30px; height: 1px; background: rgba(255,255,255,0.25);
  }
  .contact-pill svg { position: absolute; left: 8px; width: 14px; height: 14px; }

  .contact-line, .social-line {
    position: absolute; left: 393px; font-size: 17.5px; line-height: 26px; color: var(--slate); white-space: nowrap;
  }
  .contact-line--phone { top: 225px; }
  .contact-line--web { top: 254px; }
  .social-line--page { top: 311px; }
  .social-line--handle { top: 340px; }

  .social-dot {
    position: absolute; left: 352px; width: 18px; height: 18px; border-radius: 50%; background: var(--teal);
  }
  .social-dot--page { top: 315px; }
  .social-dot--handle { top: 344px; }
</style>
</head>
<body>

<section class="card card--front" aria-label="Card front">
  <svg class="floral" style="left:0;top:0" width="150" height="160" role="img" aria-label="Faint line-drawn flowers in the top left corner">
    <defs><radialGradient id="faintTL"><stop offset="0" stop-color="#1c4a50" stop-opacity="0.55"/><stop offset="1" stop-color="#1c4a50" stop-opacity="0"/></radialGradient></defs>
    <ellipse cx="55" cy="60" rx="95" ry="100" fill="url(#faintTL)"/>
  </svg>
  <svg class="floral" style="left:570px;top:0" width="209" height="195" role="img" aria-label="Large pale teal line-drawn blossoms in the top right corner">
    <defs><radialGradient id="bloomTR" cx="0.6" cy="0.45"><stop offset="0" stop-color="#3e7f84"/><stop offset="0.7" stop-color="#1b4b51"/><stop offset="1" stop-color="#0a2127" stop-opacity="0"/></radialGradient></defs>
    <ellipse cx="120" cy="90" rx="110" ry="105" fill="url(#bloomTR)"/>
  </svg>
  <svg class="floral" style="left:0;top:312px" width="130" height="133" role="img" aria-label="Pale teal line-drawn flowers in the bottom left corner">
    <defs><radialGradient id="bloomBL" cx="0.4" cy="0.6"><stop offset="0" stop-color="#3a777c"/><stop offset="0.7" stop-color="#19474d"/><stop offset="1" stop-color="#0a2127" stop-opacity="0"/></radialGradient></defs>
    <ellipse cx="55" cy="80" rx="75" ry="70" fill="url(#bloomBL)"/>
  </svg>
  <svg class="floral" style="left:690px;top:365px" width="89" height="80" role="img" aria-label="Faint line-drawn flower in the bottom right corner">
    <defs><radialGradient id="faintBR"><stop offset="0" stop-color="#1c4a50" stop-opacity="0.5"/><stop offset="1" stop-color="#1c4a50" stop-opacity="0"/></radialGradient></defs>
    <ellipse cx="50" cy="50" rx="45" ry="40" fill="url(#faintBR)"/>
  </svg>

  <div class="brand-seal">Rosalind<br>Thorpe<br>Gardens</div>
  <p class="web-address">www.<strong>RosalindThorpeGardens</strong>.example</p>
</section>

<section class="card card--back" aria-label="Card back">
  <svg class="floral" style="left:560px;top:0" width="219" height="205" role="img" aria-label="Line-drawn blossoms over soft aqua and blush washes in the top right corner">
    <defs><radialGradient id="washTR" cx="0.5" cy="0.5"><stop offset="0" stop-color="#c4f1f6"/><stop offset="0.75" stop-color="#d8f2f4"/><stop offset="1" stop-color="#ececec" stop-opacity="0"/></radialGradient></defs>
    <ellipse cx="110" cy="100" rx="110" ry="100" fill="url(#washTR)"/>
    <ellipse cx="190" cy="90" rx="35" ry="90" fill="#f6e6e1" opacity="0.8"/>
  </svg>
  <svg class="floral" style="left:0;top:330px" width="215" height="115" role="img" aria-label="Line-drawn flowers with blush and aqua petals in the bottom left corner">
    <defs><radialGradient id="washBL" cx="0.45" cy="0.6"><stop offset="0" stop-color="#f6e6e1"/><stop offset="1" stop-color="#ececec" stop-opacity="0"/></radialGradient></defs>
    <ellipse cx="90" cy="75" rx="100" ry="55" fill="url(#washBL)"/>
    <ellipse cx="175" cy="60" rx="28" ry="32" fill="#c4f1f6" opacity="0.85"/>
  </svg>

  <div class="brand-seal">Rosalind<br>Thorpe<br>Gardens</div>

  <h1 class="person"><span class="person__first">Corinne</span><span class="person__last">Haldwick</span></h1>
  <p class="person__role">OWNER</p>

  <div class="divider divider--top"></div>

  <div class="contact-pill" aria-hidden="true">
    <svg style="top:8px" viewBox="0 0 24 24"><path fill="#ffffff" d="M6.6 10.8c1.4 2.8 3.8 5.1 6.6 6.6l2.2-2.2c.3-.3.7-.4 1-.2 1.1.4 2.3.6 3.6.6.6 0 1 .4 1 1V20c0 .6-.4 1-1 1C10.6 21 3 13.4 3 4c0-.6.4-1 1-1h3.5c.6 0 1 .4 1 1 0 1.3.2 2.5.6 3.6.1.3 0 .7-.2 1L6.6 10.8z"/></svg>
    <svg style="top:39px" viewBox="0 0 24 24"><rect x="3" y="6" width="18" height="13" rx="1.5" fill="#ffffff"/><path d="M3.5 7l8.5 6.5L20.5 7" fill="none" stroke="#134d55" stroke-width="1.6"/></svg>
  </div>
  <p class="contact-line contact-line--phone">913-555-0147</p>
  <p class="contact-line contact-line--web">RosalindThorpeGardens.example</p>

  <div class="divider divider--bottom"></div>

  <span class="social-dot social-dot--page" aria-hidden="true"></span>
  <p class="social-line social-line--page">Rosalind Thorpe Gardens</p>
  <span class="social-dot social-dot--handle" aria-hidden="true"></span>
  <p class="social-line social-line--handle">@RosalindThorpeGardens</p>
</section>

</body>
</html>
```